A specialised Sport management needs a corporate brochure design

We are a specialized company in the management and consultancy of sports events. and need to have a company brochure
We provide the following services;
Event management
Venues management
Production
Ticketing
Consulting
Hospitality
Activity management
Event timing
Branding of event
Event supplies
We need a corporate profile design for our company to showcase the major events that we have covered , with images, information, statistics, surveys, products and services used. We want to highlight our professionalism and execution of the events, experience of the participants, spectators . How we have grown in the past few years and reached the international standards.
Objectives of the work:
To get sponsors and partners for future business and to present Tri-Crest
as not just a sports management company but also a professional sports
events management company.
You can check our website
www.tri-crest.example
Target Market(s)
Sponsors and corporate partners
Industry/Entity Type
Events
Requirements
Must have
- Must Have:
- - Very professional look
- -Some event images,Event information, statistics, surveys, products and services used. We want to highlight our professionalism and execution of the events (Attached)
Nice to have
- Similar momentom of the below design
- http://www.lumavent.example/wp-content/themes/lumavent/pdf/CP-2014-15-V10-Web.pdf

```html
<!DOCTYPE html>
<html lang="en">
<head>
<meta charset="utf-8">
<title>Tri-Crest Corporate Profile – Growth and Marketing Spread</title>
<link rel="stylesheet" href="https://fonts.googleapis.com/css2?family=Questrial&display=swap">
<style>
  :root {
    --backdrop: #e7e2da;
    --paper: #ffffff;
    --panel-dark: #2e2f2f;
    --orange: #f04e23;
    --orange-soft: #f26a2e;
    --amber: #e8842a;
    --red: #d7261e;
    --deep-red: #b01e1e;
    --green: #3a9e3a;
    --lime: #7ed321;
    --teal: #4fcfb4;
    --ring: #dcebea;
    --ring-edge: #b9cfcd;
    --hub: #1f4a47;
    --ink: #1c1c1c;
    --muted-line: #8a8a8a;
    --figure: #ffe6a8;
    --white: #ffffff;
  }
  * { box-sizing: border-box; margin: 0; padding: 0; }
  html, body { width: 1200px; height: 509px; overflow: hidden; background: var(--backdrop); }
  body { font-family: "Questrial", "Century Gothic", sans-serif; color: var(--ink); }
  .spread { position: relative; width: 1200px; height: 509px; }
  .spread-art { position: absolute; inset: 0; }
  .abs { position: absolute; }

  .section-title-vertical {
    left: 62px; top: 362px; transform: rotate(-90deg); transform-origin: left top;
    color: var(--teal); font-size: 18px; letter-spacing: 0.5px; white-space: nowrap;
  }
  .year { font-size: 10px; color: var(--white); width: 30px; text-align: center; line-height: 12px; }
  .ring-index { top: 242px; font-size: 16px; }

  .participant-row { left: 216px; width: 66px; height: 20px; color: var(--white); }
  .participant-row .num { position: absolute; left: 0; top: 2px; font-size: 12px; line-height: 14px; }
  .participant-row .label { position: absolute; right: 0; top: 1px; text-align: left; font-size: 8px; line-height: 9px; width: 46px; }
  .participant-row .value { color: var(--orange); }

  .marketing-title { left: 752px; top: 68px; font-size: 23px; font-weight: normal; letter-spacing: 0.5px; }
  .block-title { font-size: 14px; font-weight: normal; color: var(--orange); line-height: 16px; }
  .block-body { font-size: 11.5px; line-height: 13.2px; text-align: justify; letter-spacing: 0.3px; }
  .social-media { left: 752px; top: 122px; width: 188px; }
  .branding { left: 952px; top: 122px; width: 196px; }
  .stats-title { left: 950px; top: 231px; font-size: 19px; font-weight: normal; }

  .bubble-text { color: var(--white); text-align: center; font-size: 8px; line-height: 9.5px; }
  .bubble-text .figure { display: block; font-size: 12px; line-height: 15px; color: var(--figure); }
</style>
</head>
<body>
<main class="spread">
  <svg class="spread-art" width="1200" height="509" viewBox="0 0 1200 509">
    <defs>
      <linearGradient id="sky" x1="0" y1="0" x2="0" y2="1">
        <stop offset="0" stop-color="#c9d8e6"/>
        <stop offset="0.55" stop-color="#b98a6a"/>
        <stop offset="1" stop-color="#6c4a36"/>
      </linearGradient>
      <linearGradient id="track" x1="0" y1="0" x2="0" y2="1">
        <stop offset="0" stop-color="#a8452e"/>
        <stop offset="1" stop-color="#7d2e1f"/>
      </linearGradient>
      <linearGradient id="stands" x1="0" y1="0" x2="1" y2="0">
        <stop offset="0" stop-color="#b8473e"/>
        <stop offset="1" stop-color="#c95a4c"/>
      </linearGradient>
    </defs>

    <polygon points="30,0 1170,0 1170,478 30,490" fill="var(--paper)"/>
    <polygon points="30,20 500,20 470,440 30,440" fill="var(--panel-dark)"/>

    <polygon points="495,70 760,45 760,390 455,415" fill="url(#sky)" role="img" aria-label="Photo of an athlete climbing a rope at an obstacle event"/>

    <polygon points="75,0 1170,0 1170,20 120,98" fill="url(#stands)" role="img" aria-label="Photo of red stadium seating"/>
    <polyline points="75,0 120,98 1170,20" fill="none" stroke="var(--orange)" stroke-width="6"/>

    <polygon points="30,432 1170,360 1170,478 30,490" fill="url(#track)" role="img" aria-label="Photo of a red running track with lane lines"/>
    <line x1="30" y1="432" x2="1170" y2="360" stroke="var(--orange)" stroke-width="6"/>

    <circle cx="285" cy="255" r="146" fill="none" stroke="var(--muted-line)" stroke-width="1"/>

    <g fill="none">
      <path d="M 218 137 A 135 135 0 0 1 285 120 A 135 135 0 0 1 285 390" stroke="var(--ring-edge)" stroke-width="20"/>
      <path d="M 218 137 A 135 135 0 0 1 285 120 A 135 135 0 0 1 285 390" stroke="var(--ring)" stroke-width="16"/>
      <path d="M 232 160 A 112 112 0 0 1 397 255 A 112 112 0 0 1 285 367" stroke="var(--ring-edge)" stroke-width="20"/>
      <path d="M 232 160 A 112 112 0 0 1 397 255 A 112 112 0 0 1 285 367" stroke="var(--ring)" stroke-width="16"/>
      <path d="M 199 230 A 89 89 0 0 1 374 255 A 89 89 0 0 1 285 344" stroke="var(--ring-edge)" stroke-width="20"/>
      <path d="M 199 230 A 89 89 0 0 1 374 255 A 89 89 0 0 1 285 344" stroke="var(--ring)" stroke-width="16"/>
      <path d="M 219 255 A 66 66 0 0 1 351 255 A 66 66 0 0 1 285 321" stroke="var(--ring-edge)" stroke-width="20"/>
      <path d="M 219 255 A 66 66 0 0 1 351 255 A 66 66 0 0 1 285 321" stroke="var(--ring)" stroke-width="16"/>
    </g>
    <circle cx="285" cy="255" r="36" fill="var(--hub)"/>

    <g stroke-width="1.5">
      <line x1="205" y1="130" x2="285" y2="130" stroke="var(--amber)"/>
      <circle cx="285" cy="130" r="3" fill="var(--amber)"/>
      <line x1="168" y1="162" x2="232" y2="162" stroke="var(--teal)"/>
      <circle cx="232" cy="162" r="3" fill="var(--teal)"/>
      <line x1="141" y1="218" x2="208" y2="218" stroke="var(--red)"/>
      <circle cx="208" cy="218" r="3" fill="var(--red)"/>
      <line x1="140" y1="265" x2="228" y2="265" stroke="var(--lime)"/>
      <circle cx="228" cy="265" r="3" fill="var(--lime)"/>
    </g>
    <circle cx="205" cy="130" r="15" fill="var(--amber)"/>
    <circle cx="168" cy="162" r="15" fill="var(--teal)"/>
    <circle cx="141" cy="218" r="15" fill="var(--red)"/>
    <circle cx="140" cy="265" r="15" fill="var(--lime)"/>

    <polygon points="286,296 297,296 292,306 297,316 286,316" fill="var(--amber)"/>
    <polygon points="286,318 297,318 292,328 297,338 286,338" fill="var(--teal)"/>
    <polygon points="286,340 297,340 292,350 297,360 286,360" fill="var(--red)"/>
    <polygon points="286,362 297,362 292,372 297,382 286,382" fill="var(--lime)"/>

    <g fill="none" stroke-width="6">
      <path d="M 78 333 A 22 22 0 0 1 100 355" stroke="var(--orange)"/>
      <path d="M 100 355 A 22 22 0 0 1 70 376" stroke="var(--green)"/>
      <path d="M 70 376 A 22 22 0 0 1 78 333" stroke="#9a9a9a"/>
      <path d="M 858 63 A 22 22 0 0 1 880 85" stroke="var(--orange)"/>
      <path d="M 880 85 A 22 22 0 0 1 850 106" stroke="var(--green)"/>
      <path d="M 850 106 A 22 22 0 0 1 858 63" stroke="#9a9a9a"/>
      <path d="M 1125 220 A 22 22 0 0 1 1147 242" stroke="var(--orange)"/>
      <path d="M 1147 242 A 22 22 0 0 1 1117 263" stroke="var(--green)"/>
      <path d="M 1117 263 A 22 22 0 0 1 1125 220" stroke="#9a9a9a"/>
    </g>

    <path d="M 754 320 L 754 274 L 800 274 A 46 46 0 1 1 754 320 Z" fill="var(--orange-soft)"/>
    <path d="M 844 290 L 844 252 L 882 252 A 38 38 0 1 1 844 290 Z" fill="var(--orange)"/>
    <path d="M 910 312 L 910 272 L 950 272 A 40 40 0 1 1 910 312 Z" fill="var(--red)"/>
    <path d="M 1065 295 L 1065 255 L 1025 255 A 40 40 0 1 0 1065 295 Z" fill="var(--deep-red)"/>
    <path d="M 1156 318 L 1156 274 L 1112 274 A 44 44 0 1 0 1156 318 Z" fill="var(--orange)"/>
  </svg>

  <div class="abs section-title-vertical">GROWTH OVER THE YEARS</div>
  <div class="abs year" style="left:190px; top:124px;">2011</div>
  <div class="abs year" style="left:153px; top:156px;">2012</div>
  <div class="abs year" style="left:126px; top:212px;">2013</div>
  <div class="abs year" style="left:125px; top:259px;">2014</div>

  <div class="abs ring-index" style="left:330px; color:var(--amber);">01</div>
  <div class="abs ring-index" style="left:352px; color:var(--teal);">02</div>
  <div class="abs ring-index" style="left:375px; color:var(--red);">03</div>
  <div class="abs ring-index" style="left:398px; color:var(--lime);">04</div>

  <div class="abs participant-row" style="top:296px;"><span class="num" style="color:var(--amber)">01</span><span class="label">Participants<br><span class="value">1,300</span></span></div>
  <div class="abs participant-row" style="top:318px;"><span class="num" style="color:var(--teal)">02</span><span class="label">Participants<br><span class="value">2,700</span></span></div>
  <div class="abs participant-row" style="top:340px;"><span class="num" style="color:var(--red)">03</span><span class="label">Participants<br><span class="value">5,800+</span></span></div>
  <div class="abs participant-row" style="top:362px;"><span class="num" style="color:var(--lime)">04</span><span class="label">Participants<br><span class="value">10,000+</span></span></div>

  <h2 class="abs marketing-title">MARKETING</h2>
  <section class="abs social-media">
    <h3 class="block-title">Social Media</h3>
    <p class="block-body">With over 30,000 visitors and 10,000 participants, Tri-Crest events are the perfect opportunity to take advantage of Social Media as it’s the leading marketing tool in the industry. Take advantage of audience by engaging them in competitions and marketing campaigns.</p>
  </section>
  <section class="abs branding">
    <h3 class="block-title">Branding</h3>
    <p class="block-body">In addition to CSR benefits – companies will be mentioned in all communications and branding outlets will be prominently displayed on location and media distributions.</p>
  </section>

  <h2 class="abs stats-title">PICTORA STATISTICS</h2>
  <div class="abs bubble-text" style="left:756px; top:306px; width:88px;">Impressions during our<br>Events (Public Photos)<span class="figure">11.4 Million</span></div>
  <div class="abs bubble-text" style="left:848px; top:268px; width:68px;">Comments during<br>our Events<br>(Public Photos)<span class="figure">9,490+</span></div>
  <div class="abs bubble-text" style="left:912px; top:290px; width:76px;"><span class="figure">476+</span>Unique Contributors<br>during Our Events<br>(Public Photos)</div>
  <div class="abs bubble-text" style="left:991px; top:272px; width:68px;">Posts during our<br>Events<br>(Public Photos)<span class="figure">1,000+</span></div>
  <div class="abs bubble-text" style="left:1070px; top:294px; width:84px;">Likes generated<br>during our<br>Events (Public Photos)<span class="figure">81.25%</span></div>
</main>
</body>
</html>
```